Card Design Project

A simple, funky, cool birth announcement card
Not corporate, but arty
Not childish nor girlish
No baby pictures

Text is tbc (eg name and date may change)

Front side: just the name "fenna"
Should be easy to read

Back side text (in Dutch):

We vinden je nu al leuk!

20 JUNE 2013
Singapore

Dochter van Marieke Dorrel & Joost Vermalen

Yangon, Myanmar
+95 1 64 8319
Kletsly: Marieke.Dorrel
Kletsly: Joost.Vermalen

Size will be A6
Updates

Reason: Dear designers, At this stage we would like to have one or more designers to draft up the card (of which the final text is still tbd as the baby is yet to be born) using the typeface used on the left below (or similar!) of the newly added picture - in black - in fluorescent colours Can you get back to us in a few days? Thanks

Target Market(s)

Our funky friends in holland.

Industry/Entity Type

Baby

Requirements
Must have
• Colours, aswe are very happy to welcome this baby.
Something that makes it stand out from all other baby birth announcement cards

A6 size
Deadline 21 June
Printing will be on white (thick paper 250g)
Design for 5mm "bleedsides" all around
At least available in PDF (and other formats)
Nice to have
• We've recently moved from netherlands to Yangon
We could include the iconic kyauktaran pagoda

I would like for it to look like a cool party announcement

Include bright fluoriscent colours, including orange.
The enveloppe will be orange
Should not have
• Any baby stuff, soft pink dominance, childish stuff.

```html
<!DOCTYPE html>
<html lang="nl">
<head>
<meta charset="utf-8">
<title>Geboortekaart – We vinden je nu al leuk!</title>
<link rel="stylesheet" href="https://fonts.googleapis.com/css2?family=Caveat+Brush&family=Barlow:wght@400;700&display=swap">
<style>
  :root {
    --magenta: #e238ec;
    --hot-pink: #ff0e62;
    --lime: #b6f400;
    --cyan: #56eefb;
    --green: #62f000;
    --ink: #232323;
    --text: #333333;
    --accent: #e8155f;
    --divider-green: #7ad63a;
    --band-top: #fbfbfb;
    --band-bottom: #dcdcdc;
  }
  * { margin: 0; padding: 0; box-sizing: border-box; }
  html, body { width: 1200px; height: 799px; overflow: hidden; background: #ffffff; }
  .card {
    position: relative;
    width: 1200px;
    height: 799px;
    background: #ffffff;
    overflow: hidden;
    font-family: "Barlow", sans-serif;
  }

  .headline {
    position: absolute;
    left: 0; top: 0;
    width: 1200px;
    font-family: "Caveat Brush", cursive;
    font-weight: 400;
    line-height: 1;
  }
  .headline__line {
    position: absolute;
    white-space: nowrap;
    font-size: 232px;
    letter-spacing: -2px;
    transform: scaleX(0.845) skewX(-7deg);
    transform-origin: left bottom;
  }
  .headline__line--first { left: 192px; top: 8px; }
  .headline__line--second { left: 246px; top: 208px; }
  .word--we { color: var(--magenta); }
  .word--vinden { color: var(--hot-pink); }
  .word--je { color: var(--lime); }
  .word--nu { color: var(--cyan); }
  .word--al { color: var(--green); }
  .word--leuk { color: var(--magenta); }

  .rainbow-rule {
    position: absolute;
    left: 0; top: 503px;
    width: 1200px; height: 8px;
    background: linear-gradient(90deg, #e233ee 0%, #ff1a6a 30%, #ff5a1a 48%, #f8d800 58%, #a8f000 70%, #56eefb 100%);
  }

  .info-band {
    position: absolute;
    left: 0; top: 511px;
    width: 1200px; height: 288px;
    background: linear-gradient(180deg, var(--band-top) 0%, var(--band-bottom) 100%);
  }

  .date-box {
    position: absolute;
    left: 110px; top: 548px;
    width: 500px; height: 214px;
    border: 2px solid var(--accent);
    background: #ffffff;
    text-align: center;
  }
  .date-box::before {
    content: "";
    position: absolute;
    inset: 5px;
    border: 2px solid var(--accent);
  }
  .date-box__date {
    margin-top: 62px;
    font-weight: 700;
    font-size: 54px;
    line-height: 1;
    color: var(--accent);
    letter-spacing: 0.5px;
  }
  .date-box__place {
    margin-top: 4px;
    font-size: 23px;
    color: var(--text);
  }

  .parents {
    position: absolute;
    left: 668px; top: 548px;
  }
  .parents__title {
    font-family: "Caveat Brush", cursive;
    font-weight: 400;
    font-size: 40px;
    line-height: 43px;
    color: var(--ink);
  }
  .parents__contact {
    margin-top: 22px;
    font-size: 23px;
    line-height: 31px;
    color: var(--text);
    list-style: none;
  }
  .parents__contact .divider {
    display: inline-block;
    width: 2px; height: 20px;
    margin: 0 8px;
    vertical-align: -3px;
    background: var(--divider-green);
  }
  .chat-label {
    font-size: 17px;
    text-transform: uppercase;
    color: var(--accent);
    margin-right: 2px;
  }
</style>
</head>
<body>
<main class="card">
  <h1 class="headline">
    <span class="headline__line headline__line--first"><span class="word--we">We</span> <span class="word--vinden">vinden</span> <span class="word--je">je</span></span>
    <span class="headline__line headline__line--second"><span class="word--nu">nu</span> <span class="word--al">al</span> <span class="word--leuk">leuk!</span></span>
  </h1>

  <div class="rainbow-rule"></div>

  <section class="info-band"></section>

  <div class="date-box">
    <p class="date-box__date">20 JUNE 2013</p>
    <p class="date-box__place">Singapore</p>
  </div>

  <section class="parents">
    <h2 class="parents__title">Dochter van Marieke Dorrel<br>&amp; Joost Vermalen</h2>
    <ul class="parents__contact">
      <li>Yangon, Myanmar<span class="divider"></span>+95 1 64 8319</li>
      <li><span class="chat-label">Kletsly:</span> Marieke.Dorrel</li>
      <li><span class="chat-label">Kletsly:</span> Joost.Vermalen</li>
    </ul>
  </section>
</main>
</body>
</html>
```